RWT Fittings Ltd Business Cards

We need a business card with our business logo. We provide window and door installations on high-rises in west coast British Colombia, Canada.

I would like my business information and details on one side of the card, and the other side the company name with logo

Target Market(s)

General Contractors

Industry/Entity Type

Construction

Contact Information for Business Card

one side i want my company name and logo in the dark theme logo that i provided

Requirements
Must have
• Marco Peltieri, 16045518293, RWTFittings@mailbox-demo.com, 1407-5194 Linden Row Burnaby BC, V5H 2K9, Owner & Manager

```html
<!DOCTYPE html>
<html lang="en">
<head>
<meta charset="utf-8">
<title>RWT Fittings Ltd – Business Card</title>
<link rel="stylesheet" href="https://fonts.googleapis.com/css2?family=Open+Sans:wght@400;700&display=swap">
<style>
  :root {
    --canvas: #3a3a3c;
    --card: #1c1c1e;
    --card-deep: #141415;
    --blue: #22a7e2;
    --grey: #a3a3a6;
    --white: #f2f2f2;
    --font: "Open Sans", Arial, sans-serif;
  }
  * { margin: 0; padding: 0; box-sizing: border-box; }
  html, body { width: 1200px; height: 780px; overflow: hidden; }
  body {
    background: var(--canvas);
    font-family: var(--font);
    display: flex;
    flex-direction: column;
    align-items: center;
    justify-content: center;
    gap: 30px;
  }
  .card {
    position: relative;
    width: 620px;
    height: 355px;
    background: var(--card);
    overflow: hidden;
    box-shadow: 0 10px 28px rgba(0,0,0,.45);
  }

  /* Front */
  .accent-bar { position: absolute; background: var(--blue); }
  .accent-bar--top { left: 40px; top: 30px; width: 16px; height: 190px; }
  .accent-bar--bottom { right: 0; bottom: 0; width: 16px; height: 170px; }

  .brand {
    position: absolute;
    left: 82px;
    top: 120px;
    width: 230px;
    display: flex;
    align-items: center;
    gap: 12px;
  }
  .brand__mark { width: 34px; height: 34px; background: var(--blue); flex: none; }
  .brand__name {
    color: var(--blue);
    font-weight: 700;
    font-size: 26px;
    line-height: 1.1;
  }

  .divider {
    position: absolute;
    left: 330px;
    top: 70px;
    width: 1px;
    height: 200px;
    background: var(--blue);
  }

  .details { position: absolute; left: 350px; top: 74px; right: 30px; }
  .details__name {
    color: var(--blue);
    font-weight: 700;
    font-size: 20px;
    text-transform: uppercase;
    letter-spacing: .3px;
  }
  .details__role { color: var(--grey); font-size: 14px; margin-bottom: 12px; }
  .contact-list { list-style: none; }
  .contact-list li {
    display: flex;
    align-items: center;
    gap: 7px;
    color: var(--white);
    font-size: 13px;
    line-height: 23px;
  }
  .contact-list svg { width: 12px; height: 12px; fill: var(--blue); flex: none; }
  .details__address { color: var(--white); font-size: 13px; line-height: 19px; margin-top: 8px; }

  /* Back */
  .card--back { background: var(--card-deep); }
  .back-pattern {
    position: absolute;
    inset: 0;
    background: linear-gradient(135deg, #262628 0%, #1a1a1b 50%, #0f0f10 100%);
  }
  .back-brand {
    position: absolute;
    left: 50%;
    top: 50%;
    transform: translate(-50%, -50%);
    display: flex;
    align-items: center;
    gap: 10px;
  }
  .back-brand .brand__mark { width: 26px; height: 26px; }
  .back-brand .brand__name { font-size: 20px; }
</style>
</head>
<body>

  <section class="card card--front" aria-label="Business card front">
    <div class="accent-bar accent-bar--top"></div>
    <div class="accent-bar accent-bar--bottom"></div>

    <div class="brand">
      <span class="brand__mark"></span>
      <span class="brand__name">RWT Fittings Ltd</span>
    </div>

    <div class="divider"></div>

    <div class="details">
      <h1 class="details__name">Marco Peltieri</h1>
      <p class="details__role">Owner &amp; Manager</p>
      <ul class="contact-list">
        <li>
          <svg viewBox="0 0 24 24" aria-hidden="true"><path d="M6.6 10.8a15 15 0 0 0 6.6 6.6l2.2-2.2c.3-.3.7-.4 1-.2 1.1.4 2.3.6 3.6.6.6 0 1 .4 1 1V20c0 .6-.4 1-1 1A17 17 0 0 1 3 4c0-.6.4-1 1-1h3.5c.6 0 1 .4 1 1 0 1.3.2 2.5.6 3.6.1.3 0 .7-.2 1z"/></svg>
          16045518293
        </li>
        <li>
          <svg viewBox="0 0 24 24" aria-hidden="true"><path d="M2 5h20v14H2zM4 7v.5l8 5 8-5V7l-8 5z"/></svg>
          RWTFittings@mailbox-demo.com
        </li>
        <li>
          <svg viewBox="0 0 24 24" aria-hidden="true"><path d="M12 2a10 10 0 1 0 0 20 10 10 0 0 0 0-20zm0 2c.9 0 2.2 2 2.6 5H9.4C9.8 6 11.1 4 12 4zm-7.7 7h3.1c0 .7 0 1.4.1 2H4.3a8 8 0 0 1 0-2zm5.1 0h5.2v2H9.4zm7.2 0h3.1a8 8 0 0 1 0 2h-3.2l.1-2zM9.4 15h5.2c-.4 3-1.7 5-2.6 5s-2.2-2-2.6-5z"/></svg>
          www.rwtfittings-demo.com
        </li>
      </ul>
      <p class="details__address">1407-5194 Linden Row<br>Burnaby BC, V5H 2K9</p>
    </div>
  </section>

  <section class="card card--back" aria-label="Business card back">
    <div class="back-pattern" role="img" aria-label="Tonal repeating pattern of building outlines in dark greys"></div>
    <div class="back-brand">
      <span class="brand__mark"></span>
      <span class="brand__name">RWT Fittings Ltd</span>
    </div>
  </section>

</body>
</html>
```